Bright bears day nursery qrp limited

we would like create a website that can be updated by us easily as we have regular changes to what we provide and need. we would like something that is classy but also appealing from a child's aspect. we would be looking to add our own logo and our kinderwatch logo both attached, if you guys can create it and we will work with the preferred choice to add all the text.
We would like the links to family pathways, kinderwatch report and our chatterbook feed on the front page

we are looking for a website for our childcare business we have 2 nurseries that we would like one website.
showing our opening hours, price list, policies etc as well as photos, description of our day, staff photos and their training accreditation's.

Target Market(s)

Families

Industry/Entity Type

Childcare

Number of Pages Required

5+ page

Font styles to use
Serif

Colors

Designer to choose colors to be used in the design.

Requirements
Must have
• links to social media and other websites, photographs, links to download registration forms etc, parents able to leave reviews. google maps link, job opportunities
Nice to have
• facilities to take payments

```html
<!DOCTYPE html>
<html lang="en">
<head>
<meta charset="utf-8">
<title>Bright Bears Day Nursery</title>
<link rel="stylesheet" href="https://fonts.googleapis.com/css2?family=Play:wght@400;700&family=Raleway:wght@400;500;600;700&display=swap">
<style>
:root{
  --navy:#1c2a6b;
  --pink:#d6246e;
  --green:#5aa123;
  --ink:#2b2b2b;
  --muted:#555;
  --grey-band:#ececec;
  --dark:#3b3b3b;
  --white:#fff;
  --footer:#13246b;
}
*{box-sizing:border-box;margin:0;padding:0}
html,body{width:1200px;height:3098px;overflow:hidden}
body{font-family:"Raleway",sans-serif;color:var(--ink);background:var(--white);position:relative}
.section{position:absolute;left:0;width:1200px}
h2.title{font-family:"Play",sans-serif;font-weight:700;font-size:32px;color:var(--navy);text-align:center}
.title-rule{width:52px;height:3px;background:var(--pink);margin:10px auto 0}
.btn{display:inline-block;font-weight:600;color:#fff;text-decoration:none}

/* Header */
.site-header{top:0;height:140px}
.brand{position:absolute;left:162px;top:26px;display:flex;align-items:center;gap:14px}
.brand-mark{width:46px;height:46px;background:var(--pink);border-radius:50%}
.brand-name{font-family:"Play",sans-serif;font-weight:700;font-size:26px;color:var(--navy);line-height:1.1}
.top-actions{position:absolute;right:180px;top:20px;display:flex;align-items:center;gap:14px}
.pill{font-size:13px;padding:6px 10px;border-radius:2px}
.pill-grey{background:#5a5a5a}
.pill-green{background:var(--green)}
.top-phone{display:flex;align-items:center;gap:6px;font-family:"Play",sans-serif;font-size:21px;color:var(--navy);margin-left:4px}
.main-nav{position:absolute;right:168px;top:104px;display:flex;font-size:14px;font-weight:600}
.main-nav a{color:var(--ink);text-decoration:none;padding:0 13px;border-left:1px solid #bbb}
.main-nav a:first-child{border-left:0;color:var(--pink)}

/* Hero */
.hero{top:140px;height:480px;background:linear-gradient(90deg,#f4f4f2 0%,#eceae6 45%,#d9dfe6 70%,#eef0f2 100%)}
.hero-text{position:absolute;left:163px;top:128px;font-family:"Play",sans-serif;font-weight:700;font-size:19px;line-height:34px;color:var(--dark)}
.hero-cta{margin-top:12px;background:var(--green);font-size:13px;padding:6px 12px;font-family:"Raleway",sans-serif}
.hero-arrow{position:absolute;top:226px;width:26px;height:26px;background:#333;display:flex;align-items:center;justify-content:center}

/* Welcome */
.welcome{top:620px;height:295px;text-align:center}
.welcome h2{margin-top:36px}
.welcome .lead{font-size:14px;margin-top:22px}
.welcome .body{font-size:11px;line-height:17px;width:880px;margin:10px auto 0;color:var(--muted)}
.btn-dark{background:#2d2d2d;font-size:13px;padding:9px 22px;margin-top:18px}

/* Programs */
.programs{top:915px;height:460px;background:linear-gradient(180deg,#4e4440 0%,#6a5b55 50%,#4a3c3c 100%)}
.programs h2{color:#fff;margin-top:34px}
.program-list{position:absolute;top:140px;left:0;width:1200px}
.program{position:absolute;width:200px;text-align:center;color:#fff}
.program-photo{width:176px;height:176px;border-radius:50%;margin:0 auto;border:8px solid rgba(255,255,255,.45)}
.program h3{font-size:17px;font-weight:700;margin-top:12px}
.program .age{font-size:12px;font-weight:700;margin-top:6px}
.program p{font-size:11px;line-height:16px;margin-top:6px}

/* Why */
.why{top:1375px;height:403px;text-align:center}
.why h2{margin-top:40px}
.why .intro{font-size:12px;line-height:19px;width:860px;margin:20px auto 0;font-weight:600}
.feature-row{display:flex;justify-content:center;gap:130px;margin-top:30px}
.feature{width:120px}
.feature-icon{width:100px;height:100px;border-radius:50%;border:2px solid #bbb;margin:0 auto;display:flex;align-items:center;justify-content:center}
.feature h3{font-size:12px;font-weight:700;margin-top:16px;white-space:nowrap}
.feature p{font-size:11px;line-height:16px;color:var(--muted);margin-top:12px;width:190px;margin-left:-35px}

/* Reviews */
.reviews{top:1778px;height:384px;background:var(--grey-band);text-align:center}
.reviews h2{margin-top:38px}
.quote{font-size:11px;line-height:20px;font-style:italic;width:860px;margin:26px auto 0;color:var(--muted)}
.reviewer-photo{width:80px;height:80px;border-radius:50%;border:3px solid #e37a30;background:linear-gradient(#c7ccd6,#8a93a4);margin:12px auto 0}
.reviewer{font-size:14px;font-weight:700;color:#2b90c8;margin-top:8px}
.stars{color:#f0a81a;font-size:14px;letter-spacing:2px;margin-top:4px}
.dots{display:flex;justify-content:center;gap:4px;margin-top:6px}
.dots span{width:11px;height:11px;border-radius:50%;border:1px solid #999}

/* Gallery */
.gallery{top:2162px;height:256px;text-align:center}
.gallery h2{margin-top:38px}
.thumbs{position:absolute;top:110px;left:163px;display:flex;gap:16px}
.thumb{width:162px;height:106px;border:4px solid #fff;box-shadow:0 1px 4px rgba(0,0,0,.35);position:relative}
.thumb-caption{position:absolute;inset:0;background:rgba(40,40,40,.75);color:#fff;font-size:12px;display:flex;align-items:center;justify-content:center;text-align:center;padding:0 16px}
.gallery-arrow{position:absolute;top:2272px;font-size:24px}

/* Contact */
.contact{top:2418px;height:550px;background:linear-gradient(180deg,#3c3530 0%,#5a4a40 40%,#4b3e36 100%)}
.contact h2{color:#fff;margin-top:48px}
.contact .title-rule{background:#fff}
.info-row{position:absolute;top:122px;left:160px;width:880px;display:flex;justify-content:space-between;color:#fff;text-align:center}
.info{width:200px}
.info h3{font-size:14px;font-weight:600;margin-top:8px}
.info p{font-size:12px;font-weight:600;line-height:15px;margin-top:4px}
.enquiry{position:absolute;left:180px;top:242px;width:842px;height:297px;background:rgba(200,200,200,.55);text-align:center;color:#fff}
.enquiry h3{font-size:19px;font-weight:600;margin-top:14px}
.enquiry .sub{font-size:19px;font-weight:600;margin-top:6px}
.form{position:absolute;left:56px;top:84px;width:586px}
.field{background:rgba(255,255,255,.35);height:32px;font-size:11px;color:#333;text-align:left;padding:9px 8px;position:absolute}
.submit{position:absolute;left:56px;top:254px;width:586px;height:34px;background:var(--green);font-size:13px;font-weight:700;padding-top:9px;color:#fff}
.badge{position:absolute;left:698px;width:118px;height:112px;background:var(--navy);border-radius:4px}

/* Footer */
.site-footer{top:2968px;height:130px;background:var(--footer);color:#fff}
.foot-nav{position:absolute;left:163px;top:62px;display:flex;font-size:12px;font-weight:600}
.foot-nav a{color:#fff;text-decoration:none;padding:0 12px;border-left:1px solid #fff}
.foot-nav a:first-child{border-left:0;padding-left:4px}
.copy{position:absolute;left:163px;top:106px;font-size:10px}
.pay{position:absolute;left:884px;top:30px;font-size:12px;display:flex;align-items:center;gap:8px}
.follow{position:absolute;left:848px;top:78px;font-size:12px;display:flex;align-items:center;gap:6px}
.social{display:flex;align-items:center;gap:3px;font-size:10px}
.social i{width:14px;height:14px;border:1.5px solid #fff;border-radius:50%;display:inline-block}
</style>
</head>
<body>

<header class="section site-header">
  <div class="brand">
    <span class="brand-mark"></span>
    <span class="brand-name">Bright Bears<br>Day Nursery</span>
  </div>
  <div class="top-actions">
    <a class="btn pill pill-grey" href="#">Our Location »</a>
    <a class="btn pill pill-green" href="#">Enroll Now »</a>
    <span class="top-phone">
      <svg width="20" height="20" viewBox="0 0 24 24"><path d="M6.6 10.8a15 15 0 0 0 6.6 6.6l2.2-2.2a1 1 0 0 1 1-.25 11 11 0 0 0 3.6.6 1 1 0 0 1 1 1V20a1 1 0 0 1-1 1A17 17 0 0 1 3 4a1 1 0 0 1 1-1h3.5a1 1 0 0 1 1 1 11 11 0 0 0 .6 3.6 1 1 0 0 1-.25 1z" fill="var(--pink)"/></svg>
      123-456-7890
    </span>
  </div>
  <nav class="main-nav">
    <a href="#">Home</a><a href="#">About Us</a><a href="#">Our Services</a><a href="#">Price</a><a href="#">Gallery</a><a href="#">Contact Us</a>
  </nav>
</header>

<section class="section hero" role="img" aria-label="Photo of two toddlers playing with colourful wooden building blocks in a bright playroom">
  <div class="hero-text">
    We Specialize In Innovative, Fun-focused<br>And Premium Quality Early Childhood<br>Steam Learning Programs<br>
    <a class="btn hero-cta" href="#">Enroll Your Child Today »</a>
  </div>
  <span class="hero-arrow" style="left:8px"><svg width="10" height="12"><path d="M8 1 2 6l6 5" stroke="#fff" stroke-width="2" fill="none"/></svg></span>
  <span class="hero-arrow" style="right:8px"><svg width="10" height="12"><path d="M2 1l6 5-6 5" stroke="#fff" stroke-width="2" fill="none"/></svg></span>
</section>

<section class="section welcome">
  <h2 class="title">Welcome to Bright Bears Day Nursery</h2>
  <div class="title-rule"></div>
  <p class="lead">Our nursery is a warm, safe place where little ones learn, play and grow together every day.</p>
  <p class="body">We believe every child deserves a caring start. Our team plans each day around play, discovery and friendship, with calm routines, healthy meals and plenty of time outdoors. Families are always welcome to visit, meet our staff and see how our rooms are set up for each age group. We keep parents informed with daily notes, regular reports and open conversations so you always know how your child is getting on.</p>
  <a class="btn btn-dark" href="#">Read More</a>
</section>

<section class="section programs" role="img" aria-label="Background photo of young children at play in a classroom">
  <h2 class="title">Our Programs</h2>
  <div class="title-rule"></div>
  <div class="program-list">
    <div class="program" style="left:165px">
      <div class="program-photo" style="background:linear-gradient(#e9d6cc,#c8b2a6)" role="img" aria-label="Photo of two babies"></div>
      <h3 style="color:var(--pink)">Infant</h3><p class="age">Age 6 Weeks - 18 Months</p><p>Gentle care and sensory play for our youngest.</p>
    </div>
    <div class="program" style="left:387px">
      <div class="program-photo" style="background:linear-gradient(#d9c8d2,#9fb0c4)" role="img" aria-label="Photo of toddlers stacking toys"></div>
      <h3 style="color:#9acb2f">Toddler</h3><p class="age">Age 18 - 36 Months</p><p>Busy hands, first words and new friends.</p>
    </div>
    <div class="program" style="left:605px">
      <div class="program-photo" style="background:linear-gradient(#e0c7b2,#b98f72)" role="img" aria-label="Photo of a preschool boy smiling"></div>
      <h3 style="color:var(--pink)">Pre-School</h3><p class="age">Age 3-5 Years</p><p>Early letters, numbers and lots of stories.</p>
    </div>
    <div class="program" style="left:838px">
      <div class="program-photo" style="background:linear-gradient(#f0d9a8,#c9a36e)" role="img" aria-label="Photo of a kindergarten class with a teacher"></div>
      <h3 style="color:#9acb2f">Kindergarten</h3><p class="age">Kindergarten-12 years</p><p>Homework club, projects and outdoor fun.</p>
    </div>
  </div>
</section>

<section class="section why">
  <h2 class="title">Why Choose Us</h2>
  <div class="title-rule"></div>
  <p class="intro">Families choose us for our friendly team, thoughtful routines and bright rooms where children feel at home from their very first visit. We build confidence through play and care.</p>
  <div class="feature-row">
    <div class="feature">
      <div class="feature-icon"><svg width="44" height="44" viewBox="0 0 24 24"><path d="M12 2l3 6.5 7 .8-5.2 4.8 1.5 7-6.3-3.7-6.3 3.7 1.5-7L2 9.3l7-.8z" fill="none" stroke="#222" stroke-width="1.6"/></svg></div>
      <h3>Fun Leaning</h3><p>Playful lessons that spark curiosity each day.</p>
    </div>
    <div class="feature">
      <div class="feature-icon"><svg width="44" height="44" viewBox="0 0 24 24"><rect x="5" y="4" width="14" height="17" rx="1" fill="none" stroke="#222" stroke-width="1.6"/><path d="M8 12l3 3 5-6" fill="none" stroke="#222" stroke-width="1.8"/></svg></div>
      <h3>Easy Academics</h3><p>Gentle steps into early reading and maths.</p>
    </div>
    <div class="feature">
      <div class="feature-icon"><svg width="44" height="44" viewBox="0 0 24 24"><circle cx="12" cy="10" r="6" fill="none" stroke="#222" stroke-width="1.6"/><path d="M9.5 17h5M10 20h4" stroke="#222" stroke-width="1.6"/></svg></div>
      <h3>Innovative Approach</h3><p>Hands-on projects in science and art.</p>
    </div>
    <div class="feature">
      <div class="feature-icon"><svg width="44" height="44" viewBox="0 0 24 24"><rect x="4" y="5" width="16" height="11" fill="none" stroke="#222" stroke-width="1.6"/><path d="M12 16v4M8 20h8" stroke="#222" stroke-width="1.6"/></svg></div>
      <h3>Qualified Staff</h3><p>Trained, caring teachers you can trust.</p>
    </div>
  </div>
</section>

<section class="section reviews">
  <h2 class="title">Parent Reviews</h2>
  <div class="title-rule"></div>
  <p class="quote">“ Our daughter runs in every morning with a big smile. The staff are kind and patient, the rooms are bright and tidy, and we get lovely updates about her day. She has grown so much in confidence since joining, and we could not be happier with the care she receives here. We recommend the nursery to every family we meet. ”</p>
  <div class="reviewer-photo" role="img" aria-label="Portrait photo of the reviewer"></div>
  <p class="reviewer">- Mark Ellison</p>
  <div class="stars">★★★★</div>
  <div class="dots"><span></span><span style="background:#999"></span></div>
</section>

<section class="section gallery">
  <h2 class="title">Photo Gallery</h2>
  <div class="title-rule"></div>
  <div class="thumbs">
    <div class="thumb" style="background:linear-gradient(#f2e1c6,#d8a782)" role="img" aria-label="Photo of children playing at a table"></div>
    <div class="thumb" style="background:linear-gradient(#c6b6a4,#8a7a6a)" role="img" aria-label="Photo of a group activity"><div class="thumb-caption">Lorem Ipsum is the dummy text</div></div>
    <div class="thumb" style="background:linear-gradient(#e4d0b8,#a3b67a)" role="img" aria-label="Photo of children smiling together"></div>
    <div class="thumb" style="background:linear-gradient(#d8cdd6,#9fa9c2)" role="img" aria-label="Photo of a child with building toys"></div>
    <div class="thumb" style="background:linear-gradient(#ecd7bf,#c48f69)" role="img" aria-label="Photo of children painting"></div>
  </div>
</section>
<span class="gallery-arrow" style="left:136px">‹</span>
<span class="gallery-arrow" style="left:1052px">›</span>

<section class="section contact" role="img" aria-label="Background photo of the nursery building and garden at sunset">
  <h2 class="title">Contact Us</h2>
  <div class="title-rule"></div>
  <div class="info-row">
    <div class="info"><svg width="22" height="26" viewBox="0 0 24 28"><path d="M12 1a9 9 0 0 0-9 9c0 7 9 17 9 17s9-10 9-17a9 9 0 0 0-9-9z" fill="#fff"/><circle cx="12" cy="10" r="3.5" fill="#4b3e36"/></svg><h3>Location</h3><p>Street Name, City Name<br>State Zipcode</p></div>
    <div class="info"><svg width="24" height="26" viewBox="0 0 24 24"><rect x="2" y="5" width="20" height="14" fill="#fff"/><path d="M2 5l10 8 10-8" stroke="#4b3e36" stroke-width="1.6" fill="none"/></svg><h3>Email</h3><p>inquiry@brightbearsnursery.com</p></div>
    <div class="info"><svg width="24" height="26" viewBox="0 0 24 24"><path d="M6.6 10.8a15 15 0 0 0 6.6 6.6l2.2-2.2a1 1 0 0 1 1-.25 11 11 0 0 0 3.6.6 1 1 0 0 1 1 1V20a1 1 0 0 1-1 1A17 17 0 0 1 3 4a1 1 0 0 1 1-1h3.5a1 1 0 0 1 1 1 11 11 0 0 0 .6 3.6 1 1 0 0 1-.25 1z" fill="#fff"/></svg><h3>Call</h3><p>123-456-7890</p></div>
    <div class="info"><svg width="24" height="26" viewBox="0 0 24 24"><circle cx="12" cy="12" r="9" fill="none" stroke="#fff" stroke-width="2"/><path d="M12 7v5l3 3" stroke="#fff" stroke-width="2" fill="none"/></svg><h3>Timing</h3><p>Mon. To Sat.: 10.00 a.m. to - 04.00 p.m.<br>Sunday : Close</p></div>
  </div>
  <div class="enquiry">
    <h3>Get In Touch</h3>
    <p class="sub">Have Questions ? Well be happy To Answer!</p>
    <div class="form">
      <div class="field" style="left:0;top:0;width:284px">Name</div>
      <div class="field" style="left:302px;top:0;width:284px">Email</div>
      <div class="field" style="left:0;top:42px;width:284px">Inquiry for class</div>
      <div class="field" style="left:302px;top:42px;width:284px">Phone</div>
      <div class="field" style="left:0;top:84px;width:586px;height:76px">Inquiry message</div>
    </div>
    <div class="submit">SUBMIT</div>
    <div class="badge" style="top:12px" role="img" aria-label="Kinderwatch outstanding rating badge"></div>
    <div class="badge" style="top:142px;background:#1f3a8a" role="img" aria-label="Kinderwatch outstanding early years provider badge"></div>
  </div>
</section>

<footer class="section site-footer">
  <div class="pay"><svg width="20" height="16" viewBox="0 0 24 20"><rect x="1" y="3" width="22" height="14" rx="2" fill="none" stroke="#fff" stroke-width="1.6"/><path d="M1 7h22" stroke="#fff" stroke-width="2"/></svg>Pay Your Fees Here</div>
  <nav class="foot-nav">
    <a href="#">Home</a><a href="#">About Us</a><a href="#">Our Services</a><a href="#">Price</a><a href="#">Gallery</a><a href="#">Contact Us</a>
  </nav>
  <p class="copy">Copyright © 2017 Bright Bears Nursery School All Rights Reserved.</p>
  <div class="follow">Follow Us
    <span class="social"><i></i>Chatterbook</span>
    <span class="social"><i></i>Chirper</span>
    <span class="social"><i></i>Linkwise</span>
    <span class="social"><i></i>Globeplus</span>
  </div>
</footer>

</body>
</html>
```